Design an Office Mural for Electrical Engineering Company

We have a blank wall in our commercial office space that we would love to decorate with custom wallpaper. For this purpose, we are seeking a design to have printed as wallpaper and hung on the wall.

The design should include typography with our slogan "elevate your expectations". It is important that the design uses orange, charcoal and dark blue but other colours can also be incorporated. We want this graphic to appeal to our workforce of young, fun and intelligent men. You may like to include elements of engineering, electrical and automation in your graphic.

I have attached our logo for reference. You can choose whether or not to incorporate design elements from the logo but please DO NOT cut and paste the logo onto your design. I have attached examples of other murals that we like. Please use these as a reference for the style of your work.

The wall dimensions are 2m wide by 2.6m tall. Unfortunately we don't have a photo of the wall as it is under construction.

Target Market(s)

Young - Middle Aged Men, Tradesmen, Business People, Industrial Clients

Industry/Entity Type

Electrical engineering, factory automation, industrial maintenance

Colors
0054AA
0677BA
7BADD7
CADEEF
E8F1F8
F0912C
F2A743
F7CA91
FBE8D2
FDF5EE

Requirements
Must have
• Company colours (orange and charcoal), slogan "elevate your expectations"
Nice to have
• Hand lettering and illustration
Should not have
• The logo copy and pasted on the design. Stock images or any photographs.

```html
<!DOCTYPE html>
<html lang="en">
<head>
<meta charset="utf-8">
<title>Elevate Your Expectations – Office Mural</title>
<link rel="stylesheet" href="https://fonts.googleapis.com/css2?family=Oswald:wght@500;600;700&display=swap">
<style>
  :root {
    --backdrop: #e4e4e4;
    --charcoal: #1a1b1c;
    --charcoal-deep: #131415;
    --face-top: #c8c5c5;
    --face-left: #6e6e6e;
    --face-right: #ffffff;
    --orange: #f0912c;
    --orange-light: #f2a743;
    --circuit: #5a5a5a;
  }
  html, body {
    margin: 0;
    padding: 0;
    width: 1157px;
    height: 1200px;
    overflow: hidden;
    background: var(--backdrop);
  }
  .mural {
    position: absolute;
    left: 116px;
    top: 0;
    width: 924px;
    height: 1200px;
    display: block;
  }
  .mural-type {
    font-family: "Oswald", "Arial Narrow", sans-serif;
    font-weight: 600;
    text-transform: uppercase;
  }
  .face-top { fill: var(--face-top); }
  .face-left { fill: var(--face-left); }
  .face-right { fill: var(--face-right); }
  .face-accent { fill: var(--orange); }
</style>
</head>
<body>
<svg class="mural" viewBox="0 0 1094 1420" xmlns="http://www.w3.org/2000/svg" aria-labelledby="mural-title">
  <title id="mural-title">Elevate your expectations</title>
  <defs>
    <linearGradient id="board-fill" x1="0" y1="0" x2="0" y2="1">
      <stop offset="0" stop-color="var(--charcoal)"/>
      <stop offset="1" stop-color="var(--charcoal-deep)"/>
    </linearGradient>
    <linearGradient id="circuit-fill" x1="0" y1="0" x2="0" y2="1">
      <stop offset="0" stop-color="var(--circuit)" stop-opacity="0.35"/>
      <stop offset="1" stop-color="var(--circuit)" stop-opacity="0"/>
    </linearGradient>
    <radialGradient id="bulb-fill" cx="0.6" cy="0.4" r="0.6">
      <stop offset="0" stop-color="var(--orange-light)"/>
      <stop offset="1" stop-color="var(--orange)"/>
    </radialGradient>
  </defs>

  <rect class="board" width="1094" height="1420" fill="url(#board-fill)"/>

  <!-- circuit traces beneath the cube -->
  <rect class="circuit-traces" role="img" aria-label="Circuit board traces dripping down beneath the lettering"
        x="60" y="790" width="920" height="500" fill="url(#circuit-fill)"/>

  <!-- gear lightbulb -->
  <g class="idea-bulb" role="img" aria-label="Lightbulb made of orange gears">
    <ellipse cx="740" cy="268" rx="90" ry="62" fill="url(#bulb-fill)"/>
    <rect x="596" y="318" width="56" height="36" rx="6" fill="var(--orange)"/>
  </g>

  <!-- top face -->
  <g class="mural-type face-top">
    <text transform="matrix(0.866 -0.5 0.866 0.5 253 465)" font-size="130" textLength="439" lengthAdjust="spacingAndGlyphs">Elevate</text>
    <text transform="matrix(0.866 -0.5 0.866 0.5 403 520)" font-size="110" textLength="219" lengthAdjust="spacingAndGlyphs">Your</text>
    <text transform="matrix(0.866 -0.5 0.866 0.5 518 600)" font-size="120" textLength="566" lengthAdjust="spacingAndGlyphs">Expectation</text>
  </g>

  <!-- left face -->
  <g class="mural-type face-left">
    <text transform="matrix(0.866 0.5 0 1 148 540)" font-size="160" textLength="427" lengthAdjust="spacingAndGlyphs">Elevate</text>
    <text transform="matrix(0.866 0.5 0 1 268 775)" font-size="190" textLength="289" lengthAdjust="spacingAndGlyphs">Your</text>
    <text transform="matrix(0.866 0.5 0 1 83 800)" font-size="110" textLength="496" lengthAdjust="spacingAndGlyphs">Expectations</text>
  </g>

  <!-- right face -->
  <g class="mural-type">
    <text class="face-accent" transform="matrix(0.866 -0.5 0 1 538 750)" font-size="160" textLength="433" lengthAdjust="spacingAndGlyphs">Elevate</text>
    <text class="face-right" transform="matrix(0.866 -0.5 0 1 543 915)" font-size="190" textLength="289" lengthAdjust="spacingAndGlyphs">Your</text>
    <text class="face-right" transform="matrix(0.866 -0.5 0 1 538 1035)" font-size="105" textLength="502" lengthAdjust="spacingAndGlyphs">Expectations</text>
  </g>
</svg>
</body>
</html>
```